Vantiqo custom business card design

Need a authentic, innovative business card design for a new mobile app business. I am uploading a few screen images from our app for you to view. I would like app design theme to match business card design. I can also send logo images.

```html
<!DOCTYPE html>
<html lang="en">
<head>
<meta charset="utf-8">
<title>Vantiqo Business Card</title>
<link href="https://fonts.googleapis.com/css2?family=Montserrat:wght@800&family=Source+Sans+3:wght@400;600&display=swap" rel="stylesheet">
<style>
  :root {
    --stage: #3a302b;
    --card-white: #f6f6f4;
    --card-black: #111111;
    --pattern-dark: #1c1c1c;
    --pattern-light: #2e2e2e;
    --ink: #1a1a1a;
    --text-grey: #3b3b3b;
    --rule: #b9b9b9;
    --brand-purple: #5b0f99;
    --white: #ffffff;
  }
  * { box-sizing: border-box; margin: 0; padding: 0; }
  html, body {
    width: 1200px; height: 844px; overflow: hidden;
    background: var(--stage);
  }
  .canvas { position: relative; width: 1200px; height: 844px; }

  .card {
    position: absolute; top: 273px;
    width: 520px; height: 298px;
    border-radius: 4px;
    overflow: hidden;
  }

  /* Front */
  .card-front {
    left: 50px;
    background: var(--card-white);
    font-family: "Source Sans 3", Arial, sans-serif;
    color: var(--text-grey);
  }
  .brand {
    position: absolute; right: 28px; top: 22px;
    display: flex; flex-direction: column; align-items: center; gap: 10px;
  }
  .brand-dot {
    width: 78px; height: 78px; border-radius: 50%;
    background: var(--brand-purple);
  }
  .brand-name {
    font-family: "Montserrat", Arial, sans-serif;
    font-weight: 800; font-size: 30px; letter-spacing: -0.5px;
    color: var(--ink);
  }
  .rule {
    position: absolute; left: 24px; right: 24px;
    height: 1px; background: var(--rule);
  }
  .rule-top { top: 160px; }
  .rule-bottom { top: 238px; }
  .person { position: absolute; left: 28px; top: 168px; }
  .person-name {
    font-family: "Montserrat", Arial, sans-serif;
    font-weight: 800; font-size: 19px; letter-spacing: 0.3px;
    color: var(--brand-purple); line-height: 1.1;
  }
  .person-role { font-size: 14px; line-height: 1.2; }
  .address {
    position: absolute; left: 28px; top: 214px;
    font-size: 14px;
  }
  .contacts {
    position: absolute; left: 28px; top: 246px;
    font-size: 14px; line-height: 1.45;
  }
  .contacts .label { color: var(--brand-purple); font-weight: 600; }
  .contacts .web { color: var(--brand-purple); margin-left: 10px; }
  .contacts .item + .item { margin-left: 8px; }

  /* Back */
  .card-back {
    left: 630px;
    background: var(--card-black);
  }
  .back-pattern {
    position: absolute; inset: 0;
    background: radial-gradient(circle at 50% 50%, var(--pattern-light), var(--pattern-dark) 70%, var(--card-black));
  }
  .back-brand {
    position: absolute; left: 50%; top: 50%;
    transform: translate(-50%, -50%);
    display: flex; flex-direction: column; align-items: center; gap: 12px;
  }
  .back-brand .brand-dot { background: var(--white); width: 92px; height: 92px; }
  .back-brand .brand-name { color: var(--white); }
</style>
</head>
<body>
<main class="canvas">
  <section class="card card-front">
    <div class="brand">
      <span class="brand-dot"></span>
      <span class="brand-name">Vantiqo</span>
    </div>
    <div class="rule rule-top"></div>
    <div class="person">
      <p class="person-name">DANIEL HARROW</p>
      <p class="person-role">Managing Director</p>
    </div>
    <p class="address">48 Harbour Lane, Westbridge, Northland, 20417.</p>
    <div class="rule rule-bottom"></div>
    <div class="contacts">
      <p>
        <span class="item"><span class="label">T:</span>(044) 555 014 262</span>
        <span class="item"><span class="label">F:</span>(044) 555014264</span>
        <span class="item"><span class="label">M:</span>(044)555014263</span>
      </p>
      <p>
        <span class="label">E:</span>hello@vantiqoapp.com
        <span class="web">www.vantiqoapp.com</span>
      </p>
    </div>
  </section>

  <section class="card card-back">
    <div class="back-pattern" role="img" aria-label="Repeating glossy spot-varnish pattern of the brand symbol on black"></div>
    <div class="back-brand">
      <span class="brand-dot"></span>
      <span class="brand-name">Vantiqo</span>
    </div>
  </section>
</main>
</body>
</html>
```